Bright Harbor Counseling Letterhead for hip modern business

I would like some ombre use of the colors in the logo hip letterhead that incorporates logo colors and feel, needs to connect with young professionals and college students. i need to be able to write letters to schools to excuse absences as well. i like color blocks on one side preferably using colors from the attached logo design.

Target Market(s)

high income young people, young adults and college students

Industry/Entity Type

mental health

Font styles to use
Serif
Sans Serif

Colors
0054AA
0677BA
7BADD7
CADEEF
E8F1F8
0094D4
00A9DD
6FCCEA
C7EBF8
E9F6FB
00AB8E
00BBA5
67D7C9
C6EFE9
E9F9F6
59FF00
82FF00
B8FF75
E3FFCB
F4FFEA
A7469A
B969AE
D3A5CF
EDDBEB
F8F0F9
6B429C
8869AF
B7A5CE
E3DAEB
F3F0F8

Requirements
Must have
• a modern hip feel, somewhat color

```html
<!DOCTYPE html>
<html lang="en">
<head>
<meta charset="utf-8">
<title>Bright Harbor Counseling Letterhead</title>
<link href="https://fonts.googleapis.com/css2?family=Open+Sans:wght@300;400;700&display=swap" rel="stylesheet">
<style>
  :root {
    --backdrop: #e4dcf2;
    --paper: #ffffff;
    --ink: #4a4a4a;
    --ink-soft: #6b6b6b;
    --plum: #a7469a;
    --plum-light: #d3a5cf;
    --violet: #6b429c;
    --teal: #00bba5;
    --sky: #6fccea;
    --rule: #d8d8d8;
  }
  * { margin: 0; padding: 0; box-sizing: border-box; }
  html, body { width: 1200px; height: 784px; overflow: hidden; }
  body {
    background: var(--backdrop);
    font-family: "Open Sans", sans-serif;
    position: relative;
  }
  .letterhead {
    position: absolute;
    left: 314px;
    top: 22px;
    width: 572px;
    height: 740px;
    background: var(--paper);
    box-shadow: 0 4px 14px rgba(90, 60, 130, 0.18);
    overflow: hidden;
  }
  .color-blocks {
    position: absolute;
    left: 0;
    top: 0;
    width: 572px;
    height: 740px;
  }
  .brand {
    position: absolute;
    left: 40px;
    top: 34px;
    display: flex;
    align-items: center;
    gap: 12px;
  }
  .brand-name {
    color: var(--ink);
    font-weight: 300;
    line-height: 1.05;
  }
  .brand-name .line-main { display: block; font-size: 27px; letter-spacing: 0.5px; }
  .brand-name .line-sub { display: block; font-size: 13px; letter-spacing: 4px; padding-left: 38px; margin-top: 3px; }
  .brand-dot {
    width: 26px;
    height: 26px;
    border-radius: 50%;
    background: var(--plum);
  }
  .contact {
    position: absolute;
    left: 300px;
    top: 104px;
    padding-left: 14px;
    border-left: 1px solid var(--rule);
    list-style: none;
    font-size: 8.5px;
    line-height: 1.45;
  }
  .contact li { display: flex; align-items: flex-start; gap: 6px; color: var(--ink-soft); }
  .contact .address { color: var(--plum); font-weight: 700; }
  .contact svg { flex: none; width: 9px; height: 9px; margin-top: 2px; }
  .faint-mark {
    position: absolute;
    left: 40px;
    top: 560px;
    width: 120px;
    height: 120px;
    border-radius: 50%;
    background: radial-gradient(circle at 40% 40%, rgba(237, 219, 235, 0.7), rgba(198, 239, 233, 0.35));
  }
</style>
</head>
<body>
  <main class="letterhead">
    <svg class="color-blocks" viewBox="0 0 572 740" aria-hidden="true">
      <defs>
        <linearGradient id="ombreTop" x1="0" y1="0" x2="1" y2="0">
          <stop offset="0" stop-color="#6fccea"/>
          <stop offset="0.5" stop-color="#b969ae"/>
          <stop offset="1" stop-color="#6b429c"/>
        </linearGradient>
        <linearGradient id="ombreBottom" x1="0" y1="0" x2="1" y2="0">
          <stop offset="0" stop-color="#6b429c"/>
          <stop offset="0.5" stop-color="#b969ae"/>
          <stop offset="1" stop-color="#67d7c9"/>
        </linearGradient>
      </defs>
      <g class="top-right-block">
        <rect x="452" y="0" width="120" height="14" fill="url(#ombreTop)"/>
        <rect x="512" y="14" width="60" height="10" fill="#d3a5cf"/>
      </g>
      <g class="bottom-left-block">
        <rect x="0" y="716" width="60" height="10" fill="#c6efe9"/>
        <rect x="0" y="726" width="180" height="14" fill="url(#ombreBottom)"/>
      </g>
    </svg>

    <header class="brand">
      <p class="brand-name">
        <span class="line-main">Bright Harbor</span>
        <span class="line-sub">Counseling</span>
      </p>
      <span class="brand-dot"></span>
    </header>

    <ul class="contact">
      <li class="address">
        <svg viewBox="0 0 10 10"><circle cx="5" cy="5" r="4.5" fill="none" stroke="#a7469a"/><circle cx="5" cy="4.5" r="1.5" fill="#a7469a"/></svg>
        <span>0000 Sample Ave, Ste 210,<br>Oregon, 97201, United States</span>
      </li>
      <li>
        <svg viewBox="0 0 10 10"><circle cx="5" cy="5" r="4.5" fill="none" stroke="#a7469a"/><path d="M3.5 3 Q3 5 5.5 7 L6.5 6.2 L5.6 5.4 L5 5.8 Q4.2 5 4.2 4.3 L4.6 3.8 L4 3 Z" fill="#a7469a"/></svg>
        <span>(000) 000-0000</span>
      </li>
      <li>
        <svg viewBox="0 0 10 10"><circle cx="5" cy="5" r="4.5" fill="none" stroke="#a7469a"/><rect x="3" y="3" width="4" height="4" fill="#a7469a"/></svg>
        <span>(000) 000-0000</span>
      </li>
      <li>
        <svg viewBox="0 0 10 10"><circle cx="5" cy="5" r="4.5" fill="none" stroke="#a7469a"/><rect x="2.8" y="3.5" width="4.4" height="3" fill="none" stroke="#a7469a" stroke-width="0.8"/><path d="M2.8 3.5 L5 5.2 L7.2 3.5" fill="none" stroke="#a7469a" stroke-width="0.8"/></svg>
        <span>info@brightharbor.com</span>
      </li>
      <li>
        <svg viewBox="0 0 10 10"><circle cx="5" cy="5" r="4.5" fill="#b969ae"/></svg>
        <span>www.brightharbor.com</span>
      </li>
    </ul>

    <div class="faint-mark" role="img" aria-label="Faint soft-coloured brand decoration"></div>
  </main>
</body>
</html>
```